Varnex Consulting Business card design.

See our website www.varnexconsulting.example which will give you a good idea of what we are about. The font is called 'Play'.

I'd like a standout business card in keeping with the themes and branding on the website

Target Market(s)

professionals. HR directors

Industry/Entity Type

Business

Contact Information for Business Card

Varnex Consulting PO Box 3172 Merrowdale NSW 2291 1300 485 193 Gavin Threlkeld Principal email: career@varnexconsulting.example ABN: 71203948865

Font styles to use
Other font styles liked:
• Play

Requirements
Must have
• Must have same design colours and branding as website.
• On back I'd prefer a list of the things we do which appears below the name at the header on the website

```html
<!DOCTYPE html>
<html lang="en">
<head>
<meta charset="utf-8">
<title>Varnex Consulting – Business Card</title>
<link href="https://fonts.googleapis.com/css2?family=Play:wght@400;700&display=swap" rel="stylesheet">
<style>
  :root {
    --navy: #051d2f;
    --divider: #02080d;
    --blue: #1f8fd6;
    --white: #ffffff;
    --page: #e9e7e3;
    --photo-light: #d9dbde;
    --photo-mid: #a9adb2;
  }
  * { box-sizing: border-box; margin: 0; padding: 0; }
  html, body { width: 1200px; height: 892px; overflow: hidden; }
  body {
    background: var(--page);
    font-family: 'Play', sans-serif;
    position: relative;
  }
  .card {
    position: absolute;
    left: 280px;
    width: 640px;
    height: 388px;
    background: var(--navy);
    box-shadow: 0 6px 18px rgba(0,0,0,0.25);
    overflow: hidden;
  }
  .card--front { top: 40px; display: flex; }
  .card--back { top: 464px; }

  .front__photo {
    width: 244px;
    height: 100%;
    background: linear-gradient(160deg, var(--photo-light) 0%, var(--photo-mid) 45%, var(--photo-light) 70%, var(--photo-mid) 100%);
  }
  .front__divider { width: 9px; height: 100%; background: var(--divider); }
  .front__panel { flex: 1; padding: 34px 26px 0 28px; color: var(--white); }

  .brand {
    font-size: 30px;
    font-weight: 400;
    letter-spacing: 0.5px;
    line-height: 1;
    color: var(--white);
    white-space: nowrap;
  }
  .services {
    color: var(--blue);
    font-size: 7px;
    letter-spacing: 0.6px;
    margin-top: 6px;
    white-space: nowrap;
  }
  .person { margin-top: 44px; }
  .person__name { font-size: 24px; line-height: 1.1; }
  .person__role { font-size: 20px; line-height: 1.2; margin-top: 4px; }

  .contact { margin-top: 40px; font-size: 15px; line-height: 1.2; }
  .contact__abn { color: var(--blue); font-size: 16px; margin-bottom: 8px; }
  .contact__row { display: flex; align-items: center; gap: 12px; margin-bottom: 9px; }
  .contact__icon { width: 14px; height: 14px; flex: none; }

  .back__brand {
    position: absolute;
    left: 0; right: 0;
    top: 150px;
    text-align: center;
    font-size: 48px;
    font-weight: 400;
    letter-spacing: 1px;
    color: var(--blue);
    white-space: nowrap;
  }
  .back__services {
    position: absolute;
    left: 0; right: 0;
    top: 222px;
    text-align: center;
    color: var(--blue);
    font-size: 15px;
    letter-spacing: 1.5px;
    white-space: nowrap;
  }
  .sep { margin: 0 8px; }
</style>
</head>
<body>
  <section class="card card--front">
    <div class="front__photo" role="img" aria-label="Photograph of a surfer in a wetsuit riding through white water spray"></div>
    <div class="front__divider"></div>
    <div class="front__panel">
      <div class="brand">VARNEX CONSULTING</div>
      <div class="services">Search &amp; Select | Career | Coaching | Leadership | Outplacement</div>
      <div class="person">
        <div class="person__name">Gavin Threlkeld</div>
        <div class="person__role">Principal</div>
      </div>
      <div class="contact">
        <div class="contact__abn">ABN: 71203948865</div>
        <div class="contact__row">
          <svg class="contact__icon" viewBox="0 0 14 14"><rect width="14" height="14" fill="#fff"/><path d="M4 3.5 L5.5 3.5 L6.2 5.5 L5.2 6.3 Q6 8 7.7 8.8 L8.5 7.8 L10.5 8.5 L10.5 10 Q6 10.5 3.5 5 Z" fill="#051d2f"/></svg>
          <span>1300 485 193</span>
        </div>
        <div class="contact__row">
          <svg class="contact__icon" viewBox="0 0 14 14"><rect width="14" height="14" fill="#fff"/><rect x="3" y="4.5" width="8" height="5.5" fill="none" stroke="#051d2f" stroke-width="1.1"/><path d="M3 4.5 L7 7.5 L11 4.5" fill="none" stroke="#051d2f" stroke-width="1.1"/></svg>
          <span>career@varnexconsulting.example</span>
        </div>
        <div class="contact__row">
          <svg class="contact__icon" viewBox="0 0 14 14"><rect width="14" height="14" fill="#fff"/><path d="M7 11.5 L4.4 7.2 A3 3 0 1 1 9.6 7.2 Z" fill="#051d2f"/><circle cx="7" cy="5.6" r="1.1" fill="#fff"/></svg>
          <span>PO Box 3172 Merrowdale NSW 2291</span>
        </div>
      </div>
    </div>
  </section>

  <section class="card card--back">
    <div class="back__brand">VARNEX CONSULTING</div>
    <div class="back__services">Search &amp; Select<span class="sep">|</span>Career<span class="sep">|</span>Coaching<span class="sep">|</span>Leadership<span class="sep">|</span>Outplacement</div>
  </section>
</body>
</html>
```